Design and Renovation Company Luxury Business Card

I want to create a luxury business card for a Design and Renovation Firm . We will use our current logo. The company name is 528BUILDA. We do not want anything standard. We need a very unique concept.
Please see uploaded inspiration. I really like the textured paper option. I would like the card to be thick with debossing, and/or embossing options. The logo has orange in it but I would like to see the card with and without the orange. I think the orange may make the company feel less high-end. The goal is to elevate the logo not match its vibe per se of the logo. We want something very unique, not standard at all!
I would like a space for :
Logo,
Name,
Position,
Email,
Office number,
Website Address,
Business Address,
Thank you!
Have fun!
Target Market(s)
Home owners Age 35 +
Industry/Entity Type
Design and Renovation
Contact Information for Business Card
Logo, Name, Position, Email, Office number, Website Address, Business Address,.
Colors
Designer to choose colors to be used in the design.
Requirements
Must have
- A luxury designer feel. Must be black or dark grey but open to other luxury ideas.
Nice to have
- Gold, silver, black embossing or debossing. Textured paper design.
Should not have
- A cheap look and feel.

```html
<!DOCTYPE html>
<html lang="en">
<head>
<meta charset="utf-8">
<title>528BUILDA Business Card</title>
<link href="https://fonts.googleapis.com/css2?family=Questrial&family=Montserrat:wght@600;700&display=swap" rel="stylesheet">
<style>
  :root {
    --page: #f1f1f1;
    --card-dark: #0b0b0b;
    --card-mid: #262626;
    --gold: #d9b866;
    --gold-line: #a88a45;
    --icon-glyph: #141414;
  }
  * { margin: 0; padding: 0; box-sizing: border-box; }
  html, body { width: 1200px; height: 1200px; overflow: hidden; }
  body {
    background: var(--page);
    font-family: "Questrial", "Helvetica Neue", Arial, sans-serif;
    position: relative;
  }
  .card {
    position: absolute;
    left: 160px;
    width: 880px;
    height: 502px;
    overflow: hidden;
    box-shadow: 0 24px 50px rgba(0,0,0,0.35);
    color: var(--gold);
  }
  .card--front { top: 72px; }
  .card--back { top: 626px; }
  .card__texture {
    position: absolute; inset: 0;
    background:
      radial-gradient(ellipse at 50% 0%, rgba(255,255,255,0.07), transparent 70%),
      linear-gradient(180deg, var(--card-mid) 0%, #161616 45%, var(--card-dark) 100%);
  }
  .card__frame {
    position: absolute;
    inset: 25px;
    border: 1px solid var(--gold-line);
  }
  /* Front */
  .brand {
    position: absolute;
    left: 0; right: 0; top: 206px;
    display: flex; flex-direction: column; align-items: center;
  }
  .brand__name {
    font-size: 70px; line-height: 1; letter-spacing: 3px;
  }
  .brand__tagline {
    font-size: 17px; letter-spacing: 4.6px; margin-top: 6px;
  }
  .website {
    position: absolute; right: 70px; bottom: 58px;
    font-size: 21px; letter-spacing: 0.5px;
  }
  /* Back */
  .person { position: absolute; left: 518px; top: 58px; }
  .person__name {
    font-family: "Montserrat", "Helvetica Neue", Arial, sans-serif;
    font-weight: 700; font-size: 39px; letter-spacing: 4px; line-height: 1.1;
    padding-bottom: 4px; border-bottom: 2px solid var(--gold);
  }
  .person__title {
    font-family: "Montserrat", "Helvetica Neue", Arial, sans-serif;
    font-weight: 600; font-size: 17px; margin-top: 6px;
  }
  .back-brand {
    position: absolute; left: 140px; top: 372px;
    font-size: 30px; letter-spacing: 2px; line-height: 1;
  }
  .contacts {
    position: absolute; left: 517px; top: 230px; list-style: none;
  }
  .contacts__item {
    display: flex; align-items: flex-start; gap: 16px;
    font-size: 21px; letter-spacing: 2px; line-height: 24px;
    margin-bottom: 14px;
  }
  .contacts__icon { width: 28px; height: 28px; flex: none; margin-top: -2px; }
</style>
</head>
<body>

<section class="card card--front">
  <div class="card__texture" role="img" aria-label="Black quilted diamond paper texture"></div>
  <div class="card__frame"></div>
  <div class="brand">
    <span class="brand__name">528BUILDA</span>
    <span class="brand__tagline">Design and Renovation Firm</span>
  </div>
  <p class="website">www.yourwebsite.com</p>
</section>

<section class="card card--back">
  <div class="card__texture" role="img" aria-label="Black quilted diamond paper texture"></div>
  <div class="card__frame"></div>

  <div class="person">
    <h1 class="person__name">Your Name</h1>
    <p class="person__title">Your Title</p>
  </div>

  <p class="back-brand">528BUILDA</p>

  <ul class="contacts">
    <li class="contacts__item">
      <svg class="contacts__icon" viewBox="0 0 28 28" aria-hidden="true">
        <circle cx="14" cy="14" r="14" fill="var(--gold)"/>
        <path d="M9 7.5c1-.6 2-.2 2.5.8l1 2c.3.7.1 1.4-.5 1.8l-.8.6c.6 1.6 1.8 2.8 3.4 3.5l.6-.8c.4-.6 1.2-.8 1.8-.5l2 1c1 .5 1.3 1.6.7 2.5-.8 1.2-2.2 1.8-3.6 1.3-3.7-1.3-6.4-4-7.7-7.7-.5-1.4.2-3 1.6-3.5z" fill="var(--icon-glyph)"/>
      </svg>
      <span>Your Phone Number</span>
    </li>
    <li class="contacts__item">
      <svg class="contacts__icon" viewBox="0 0 28 28" aria-hidden="true">
        <circle cx="14" cy="14" r="14" fill="var(--gold)"/>
        <g fill="none" stroke="var(--icon-glyph)" stroke-width="1.4">
          <circle cx="14" cy="14" r="7"/>
          <ellipse cx="14" cy="14" rx="3" ry="7"/>
          <line x1="7" y1="14" x2="21" y2="14"/>
          <line x1="8" y1="10.5" x2="20" y2="10.5"/>
          <line x1="8" y1="17.5" x2="20" y2="17.5"/>
        </g>
      </svg>
      <span>Your Email Address</span>
    </li>
    <li class="contacts__item">
      <svg class="contacts__icon" viewBox="0 0 28 28" aria-hidden="true">
        <circle cx="14" cy="14" r="14" fill="var(--gold)"/>
        <rect x="7.5" y="9.5" width="13" height="9" rx="1" fill="var(--icon-glyph)"/>
        <path d="M8 10.2l6 4.6 6-4.6" fill="none" stroke="var(--gold)" stroke-width="1.2"/>
      </svg>
      <span>Your Site Here</span>
    </li>
    <li class="contacts__item">
      <svg class="contacts__icon" viewBox="0 0 28 28" aria-hidden="true">
        <circle cx="14" cy="14" r="14" fill="var(--gold)"/>
        <path d="M14 6.5a5.5 5.5 0 0 1 5.5 5.5c0 4-5.5 9.5-5.5 9.5S8.5 16 8.5 12A5.5 5.5 0 0 1 14 6.5z" fill="var(--icon-glyph)"/>
        <circle cx="14" cy="12" r="2" fill="var(--gold)"/>
      </svg>
      <span>Your Address Here<br>Your Street Name<br>Your Country</span>
    </li>
  </ul>
</section>

</body>
</html>
```